Destination PDF Template (Editable)

Objective: Create a visually stunning and compelling PDF brochure that showcases The Vorelka Crest Lodge as the ultimate luxury hunting destination in Kyrgyzstan, specializing in Marco Polo and Ibex hunts. The PDF should evoke a sense of exclusivity, adventure, and the breathtaking beauty of the Tian Shan mountains, ultimately driving bookings.
Target Audience: High-net-worth individuals, discerning hunters seeking exceptional experiences, adventure travelers, and those interested in unique and luxurious wilderness experiences.
Overall Tone & Style: Sophisticated, elegant, and aspirational. Think high-end travel magazines combined with a touch of rugged adventure. Avoid anything that feels generic or overly commercial. The design should reflect the unparalleled nature of the lodge and the hunts offered. (I'm attaching a reference PDF that i like), as well as another instructions file. Drive link for photos: https://files.pondery-share.net/box/folders/7KqLm2xVbR4tWz9hN3cJpE6yF0aDs8uG?mode=open
Another Link: https://files.pondery-share.net/box/u/0/folders/9ZtRe4wQmN2bVx7kLp5sHc8jYd3fGa1oU

```html
<!DOCTYPE html>
<html lang="en">
<head>
<meta charset="UTF-8">
<title>Hunt Details</title>
<link rel="stylesheet" href="https://fonts.googleapis.com/css2?family=Poppins:wght@400;600;700&family=Source+Sans+3:wght@400&display=swap">
<style>
  :root {
    --page-bg: #f4f4f3;
    --heading: #13303e;
    --body-text: #2f3438;
    --hero-white: #ffffff;
    --sky-top: #3f79c6;
    --sky-cloud: #c9d4de;
    --rock: #8a5a44;
    --meadow: #4f5a34;
    --map-sand: #ebe7df;
    --map-green: #cdeedd;
  }
  * { margin: 0; padding: 0; box-sizing: border-box; }
  html, body { width: 1200px; height: 675px; overflow: hidden; background: var(--page-bg); }
  .page { position: relative; width: 1200px; height: 675px; background: var(--page-bg); }

  .hero {
    position: absolute; left: 0; top: 0; width: 1200px; height: 291px;
    background: linear-gradient(180deg, var(--sky-top) 0%, var(--sky-cloud) 38%, var(--rock) 62%, var(--meadow) 100%);
  }
  .hero-title {
    position: absolute; left: 33px; top: 190px;
    font-family: 'Poppins', sans-serif; font-weight: 700; font-size: 57px;
    color: var(--hero-white); letter-spacing: -0.5px; line-height: 1.2;
  }

  .column { position: absolute; top: 362px; width: 242px; text-align: center; }
  .col-highlights { left: 52px; }
  .col-property { left: 369px; }
  .col-getting { left: 693px; }

  .column h2 {
    font-family: 'Poppins', sans-serif; font-weight: 600; font-size: 39px;
    color: var(--heading); letter-spacing: -2px; line-height: 1.2; white-space: nowrap;
    margin-left: -30px; margin-right: -30px;
  }
  .column h3 {
    font-family: 'Poppins', sans-serif; font-weight: 400; font-size: 25px;
    color: var(--heading); letter-spacing: -1px; line-height: 1.3; white-space: nowrap;
    margin: 4px -30px 18px;
  }
  .column p {
    font-family: 'Source Sans 3', sans-serif; font-size: 10px; line-height: 18.1px;
    color: var(--body-text); text-align: justify; text-align-last: center;
  }
  .column p + p { margin-top: 18px; }

  .route-map {
    position: absolute; left: 974px; top: 347px; width: 201px; height: 287px;
    background: linear-gradient(160deg, var(--map-sand) 0%, var(--map-sand) 45%, var(--map-green) 70%, var(--map-sand) 100%);
  }
</style>
</head>
<body>
<main class="page">
  <header class="hero" role="img" aria-label="Photograph of the Tian Shan mountains under a blue sky with clouds and a setting sun">
    <h1 class="hero-title">Hunt Details</h1>
  </header>

  <section class="column col-highlights">
    <h2>Highlights</h2>
    <p>Experience an unforgettable hunting adventure in Kyrgyzstan’s majestic Tian Shan Mountains. Pursue the elusive Marco Polo sheep and Siberian Ibex, hunting on horseback alongside seasoned local guides. Sharpen your long-range shooting skills, as accuracy at 400-500 meters may be required. The breathtaking scenery, from towering peaks to vast valleys, provides a stunning backdrop.</p>
    <p>This unique combination of challenging hunts and unparalleled landscapes creates a truly once-in-a-lifetime experience.</p>
  </section>

  <section class="column col-property">
    <h2>Property Facts</h2>
    <p>Nestled deep within the majestic Tian Shan mountains, this hunting camp, a unique endeavor by the Kyrgyz government, offers an unparalleled wilderness experience. While the eight luxurious rooms each provide private bathrooms and unexpected amenities like reliable WiFi – a true rarity in such a remote setting – it’s the communal spaces that truly capture the grandeur of the surroundings.</p>
    <p>The lounge area, with its striking floor-to-ceiling windows, frames breathtaking panoramic views of the rugged landscape. This blend of modern comforts and unspoiled wilderness creates a hunting retreat unlike any other.</p>
  </section>

  <section class="column col-getting">
    <h2>Getting There</h2>
    <h3>Recommended Route</h3>
    <p>International flights typically arrive at Manas International Airport (FRU) in Bishkek, Kyrgyzstan, often with layovers in Istanbul or Dubai. Upon arrival, our team will assist with firearms clearance. For guests arriving late, overnight accommodations in Bishkek can be arranged.</p>
    <p>From Bishkek, hunters have two options to reach the hunting area in the mountains: a 12-hour scenic drive or a 2.5-hour helicopter flight.</p>
  </section>

  <div class="route-map" role="img" aria-label="Map of the Issyk-Kul and Naryn regions with a pin marking the hunting area"></div>
</main>
</body>
</html>
```